Silver Bloom Marisol's Cleaning Service Business Cards Project

A business card with all contact details with logo design on there (already have a logo) eye catching Logo and contact info on one side, full logo on the back, must target upper class residential and corporate companies, fitness companies, still keep it on the feminine side of things , must look elegant

Target Market(s)

Upper class homes and corporate companies

Industry/Entity Type

Cleaning Service

Contact Information for Business Card

Name: Marisol Quenby
Position: Director
ABN: 31647209853
Email: marisolssilvercleaning@tidymail.example
Number: 0417906354

Font styles to use
Decorative

Colors

Designer to choose colors to be used in the design.

Requirements
Must have
• Available Sydney Wide, contact info and logo on one side, full logo on the back
Nice to have
• Professional appearance
Should not have
• Cheap advert looking stuff

```html
<!DOCTYPE html>
<html lang="en">
<head>
<meta charset="utf-8">
<title>Silver Bloom – Business Cards</title>
<link href="https://fonts.googleapis.com/css2?family=Cinzel:wght@500&family=Lato:wght@400&display=swap" rel="stylesheet">
<style>
  :root {
    --backdrop: #2b2b2b;
    --card: #0f0f0f;
    --card-edge: #181818;
    --teal: #2fe6da;
    --white: #f2f2f2;
    --divider: #555555;
  }
  * { box-sizing: border-box; margin: 0; padding: 0; }
  html, body { width: 1200px; height: 900px; overflow: hidden; }
  body {
    background: var(--backdrop);
    position: relative;
    font-family: "Lato", Arial, sans-serif;
  }
  .card {
    position: absolute;
    width: 540px;
    height: 310px;
    background: linear-gradient(160deg, var(--card-edge), var(--card) 60%);
    border-radius: 3px;
    overflow: hidden;
  }
  .card::after {
    content: "";
    position: absolute;
    left: 0; right: 0; bottom: 0;
    height: 10px;
    background: var(--teal);
  }
  .card--front { left: 360px; top: 100px; }
  .card--back { left: 180px; top: 480px; }

  .brand {
    position: absolute;
    inset: 0 0 10px 0;
    display: flex;
    flex-direction: column;
    align-items: center;
    justify-content: center;
    gap: 10px;
    font-family: "Cinzel", Georgia, serif;
    font-weight: 500;
    color: var(--teal);
    text-transform: uppercase;
  }
  .brand__name { font-size: 34px; letter-spacing: 1px; }
  .brand__line { font-size: 12px; letter-spacing: 4px; }
  .brand__dot {
    width: 14px; height: 14px;
    border: 1.5px solid var(--teal);
    border-radius: 50%;
  }

  .back-mark {
    position: absolute;
    left: 30px; top: 70px;
    width: 160px; height: 160px;
    display: flex;
    flex-direction: column;
    align-items: center;
    justify-content: center;
    gap: 8px;
    font-family: "Cinzel", Georgia, serif;
    font-weight: 500;
    color: var(--teal);
    text-transform: uppercase;
    text-align: center;
  }
  .back-mark__name { font-size: 20px; line-height: 1.2; }
  .divider {
    position: absolute;
    left: 215px; top: 75px;
    width: 1px; height: 130px;
    background: var(--divider);
  }
  .contact {
    position: absolute;
    left: 240px; top: 78px;
    color: var(--white);
  }
  .contact__name {
    font-family: "Cinzel", Georgia, serif;
    font-weight: 500;
    font-size: 22px;
    color: var(--teal);
    letter-spacing: 0.5px;
  }
  .contact__role { font-size: 15px; margin-top: 2px; }
  .contact__abn { font-size: 15px; margin-top: 20px; }
  .contact__abn span { color: var(--teal); }
  .contact__row {
    display: flex; align-items: center; gap: 8px;
    font-size: 15px; margin-top: 12px;
  }
  .contact__row + .contact__row { margin-top: 4px; }
  .contact__row svg { width: 12px; height: 12px; flex: none; }
</style>
</head>
<body>
  <section class="card card--front" aria-label="Card front">
    <div class="brand">
      <div class="brand__dot"></div>
      <div class="brand__name">Silver Bloom</div>
      <div class="brand__line">Marisol's Cleaning Service</div>
    </div>
  </section>

  <section class="card card--back" aria-label="Card back">
    <div class="back-mark">
      <div class="brand__dot"></div>
      <div class="back-mark__name">Silver<br>Bloom</div>
    </div>
    <div class="divider"></div>
    <div class="contact">
      <div class="contact__name">MARISOL QUENBY</div>
      <div class="contact__role">Director</div>
      <div class="contact__abn"><span>ABN:</span> 31647209853</div>
      <div class="contact__row">
        <svg viewBox="0 0 12 12" aria-hidden="true"><path fill="#2fe6da" d="M1 3.5C1 2 3 1.5 6 1.5S11 2 11 3.5V5H8.5V3.8h-5V5H1zM3 6h6l1.5 4.5h-9z"/></svg>
        0417906354
      </div>
      <div class="contact__row">
        <svg viewBox="0 0 12 12" aria-hidden="true"><rect x="0.5" y="2" width="11" height="8" fill="#2fe6da"/><path d="M0.5 2.5L6 6.5L11.5 2.5" stroke="#0f0f0f" stroke-width="1" fill="none"/></svg>
        marisolssilvercleaning@tidymail.example
      </div>
    </div>
  </section>
</body>
</html>
```